DOUBLE SIDED BROCHURE NEEDED TO PROMOTE DOCTOR

I need a double sided DL size (99mm x 210mm) brochure, promoting a doctor seeing patients in a new area.

I want something professional. I have included the relevant information. I would also like the Dr's picture somwhere in the brochure, with a professional background. I wish to print these tomorrow, so i will pick a winner within 14 hours of posting this ad.

I have included an example of a brochures design that I recently saw, and its definietly a good starting point.

Industry/Entity Type

Medical

```html
<!DOCTYPE html>
<html lang="en">
<head>
<meta charset="utf-8">
<title>Dr. Karam – Endocrine, Breast and General Surgery</title>
<link href="https://fonts.googleapis.com/css2?family=Almendra:wght@400;700&family=Arimo:wght@400;700&family=Open+Sans:wght@400&display=swap" rel="stylesheet">
<style>
  :root {
    --green-dark: #1d7f45;
    --green-rule: #23904f;
    --green-band: #4cb87a;
    --ink: #111111;
    --body-ink: #222222;
    --white: #ffffff;
    --steth-blue: #2b3fd6;
    --photo-tone: #6e6a66;
  }
  * { margin: 0; padding: 0; box-sizing: border-box; }
  html, body {
    width: 1200px;
    height: 2473px;
    overflow: hidden;
    background: var(--white);
  }
  .brochure {
    position: relative;
    width: 1200px;
    height: 2473px;
    background: var(--white);
    overflow: hidden;
  }
  .intro {
    position: absolute;
    left: 86px;
    top: 4px;
    width: 1048px;
    font-family: "Arimo", Arial, sans-serif;
    font-weight: 700;
    font-size: 45px;
    line-height: 61px;
    color: var(--green-dark);
    text-align: justify;
  }
  .service-list {
    position: absolute;
    list-style: none;
    font-family: "Open Sans", Arial, sans-serif;
    font-size: 44px;
    color: var(--body-ink);
  }
  .service-list li {
    position: absolute;
    left: 0;
    white-space: nowrap;
    line-height: 60px;
  }
  .service-list li::before {
    content: "";
    position: absolute;
    width: 14px;
    height: 14px;
    border-radius: 50%;
    background: var(--ink);
    top: 30px;
  }
  .specialties { left: 0; top: 0; }
  .specialties li { padding-left: 145px; }
  .specialties li::before { left: 80px; }
  .specialties .thyroid { top: 250px; }
  .specialties .parathyroid { top: 374px; padding-left: 137px; }
  .specialties .parathyroid span { display: block; }
  .specialties .breast { top: 542px; padding-left: 148px; }

  .divider {
    position: absolute;
    left: 0;
    top: 791px;
    width: 1200px;
    height: 28px;
    background: var(--green-rule);
  }
  .cross-badge {
    position: absolute;
    left: 490px;
    top: 651px;
    width: 220px;
    height: 220px;
  }
  .stethoscope {
    position: absolute;
    left: 272px;
    top: 849px;
    width: 631px;
    height: 423px;
    background: radial-gradient(ellipse at 40% 55%, rgba(43,63,214,0.55), rgba(43,63,214,0.12) 70%, rgba(255,255,255,0) 100%);
  }
  .headline {
    position: absolute;
    left: 0;
    width: 1200px;
    text-align: center;
    font-family: "Almendra", "Palatino Linotype", serif;
    font-weight: 400;
    color: var(--ink);
    white-space: nowrap;
  }
  .headline .line-one {
    position: absolute;
    left: 0; width: 1200px;
    top: 1290px;
    font-size: 150px;
    line-height: 170px;
  }
  .headline .line-two {
    position: absolute;
    left: 0; width: 1200px;
    top: 1460px;
    font-size: 124px;
    line-height: 150px;
  }
  .general li { padding-left: 161px; }
  .general li::before { left: 93px; }
  .general .g1 { top: 1737px; }
  .general .g2 { top: 1850px; }
  .general .g3 { top: 1966px; }
  .general .g4 { top: 2081px; }
  .general .g5 { top: 2196px; }

  .portrait {
    position: absolute;
    left: 651px;
    top: 1664px;
    width: 549px;
    height: 775px;
    background: linear-gradient(180deg, #8c857f 0%, var(--photo-tone) 45%, #1e2230 100%);
  }
  .footer-band {
    position: absolute;
    left: 0;
    top: 2439px;
    width: 1200px;
    height: 34px;
    background: var(--green-band);
  }
</style>
</head>
<body>
<main class="brochure">
  <p class="intro">Dr. Karam is a highly trained specialised surgeon, in all areas of Endocrine, Breast and General Surgery.</p>

  <ul class="service-list specialties">
    <li class="thyroid">Thyroid Surgery</li>
    <li class="parathyroid"><span>Parathyroid surgery (including minimally</span><span>invasive parathyroidectomy)</span></li>
    <li class="breast">Breast Cancer Benign breast lesions</li>
  </ul>

  <div class="divider"></div>
  <svg class="cross-badge" viewBox="0 0 220 220" aria-hidden="true">
    <circle cx="110" cy="110" r="108" fill="var(--green-rule)"/>
    <rect x="84" y="22" width="52" height="176" fill="var(--white)"/>
    <rect x="22" y="84" width="176" height="52" fill="var(--white)"/>
  </svg>

  <div class="stethoscope" role="img" aria-label="Blue stethoscope illustration"></div>

  <h1 class="headline">
    <span class="line-one">All areas of</span>
    <span class="line-two">general surgery</span>
  </h1>

  <ul class="service-list general">
    <li class="g1">Gallbladder surgery</li>
    <li class="g2">Hernia surgery</li>
    <li class="g3">Haemorrhoids</li>
    <li class="g4">Carpal Tunnel</li>
    <li class="g5">Vasectomy etc etc…</li>
  </ul>

  <div class="portrait" role="img" aria-label="Portrait photograph of the doctor in a dark jacket and checked shirt"></div>

  <div class="footer-band"></div>
</main>
</body>
</html>
```